New Company Business Card design

Looking for a corporate looking business card utilising my new logo design - the logo i would like embossed as one option and flat as another - simplistic but stylish - less is more - we are an import export business launching into the market - i would like a couple of options as main background - Grey or Black

```html
<!DOCTYPE html>
<html lang="en">
<head>
<meta charset="utf-8">
<title>Meridian Trade Co. — Business Card</title>
<link rel="stylesheet" href="https://fonts.googleapis.com/css2?family=Roboto:wght@400;500;700&display=swap">
<style>
  :root {
    --backdrop: #d8d3cb;
    --card-white: #f6f6f6;
    --card-black: #1b1c1d;
    --brand-blue: #1a78c2;
    --text-grey: #555a5e;
    --text-dark: #4a4f53;
    --white: #ffffff;
  }
  * { margin: 0; padding: 0; box-sizing: border-box; }
  html, body {
    width: 1200px; height: 960px; overflow: hidden;
    background: var(--backdrop);
    font-family: "Roboto", Arial, sans-serif;
  }
  .canvas { position: relative; width: 1200px; height: 960px; }
  .card { position: absolute; box-shadow: 0 3px 8px rgba(0,0,0,.35); }

  .card-front {
    left: 315px; top: 113px; width: 600px; height: 343px;
    background: var(--card-white);
  }
  .brand {
    position: absolute; left: 38px; top: 44px;
    display: flex; align-items: center; gap: 12px;
    color: var(--brand-blue); font-weight: 700; font-size: 26px;
    letter-spacing: .5px;
  }
  .brand-dot { width: 22px; height: 22px; border-radius: 50%; background: var(--brand-blue); }
  .holder { position: absolute; right: 46px; top: 38px; text-align: right; }
  .holder-name { color: var(--brand-blue); font-weight: 500; font-size: 21px; line-height: 1.1; }
  .holder-role { color: var(--text-grey); font-size: 14px; line-height: 1.3; }
  .accent-tab {
    position: absolute; right: 0; top: 38px; width: 12px; height: 38px;
    background: var(--brand-blue);
  }
  .address {
    position: absolute; left: 38px; top: 194px;
    color: var(--text-dark); font-size: 14px; line-height: 18px;
  }
  .contacts {
    position: absolute; left: 38px; top: 238px; list-style: none;
    color: var(--text-dark); font-size: 14px;
  }
  .contacts li { display: flex; align-items: center; height: 19px; }
  .contacts svg { width: 14px; height: 14px; margin-right: 9px; fill: var(--brand-blue); }

  .card-back {
    left: 311px; top: 472px; width: 600px; height: 343px;
    background: var(--card-black);
  }
  .back-brand {
    position: absolute; left: 0; right: 0; top: 118px;
    display: flex; justify-content: center; align-items: center; gap: 22px;
    color: var(--white); font-weight: 700; font-size: 64px; letter-spacing: 2px;
  }
  .back-brand-dot { width: 52px; height: 52px; border-radius: 50%; background: var(--white); }
  .website {
    position: absolute; right: 38px; top: 296px;
    color: var(--white); font-size: 14px;
  }
</style>
</head>
<body>
<main class="canvas">
  <section class="card card-front">
    <div class="brand"><span class="brand-dot"></span>Meridian Trade Co.</div>
    <div class="holder">
      <p class="holder-name">DANIEL CARTER</p>
      <p class="holder-role">CEO/FOUNDER</p>
    </div>
    <div class="accent-tab"></div>
    <p class="address">214 Harbor View Road<br>Portfield, Oregon 97120</p>
    <ul class="contacts">
      <li><svg viewBox="0 0 24 24"><path d="M6.6 10.8a15 15 0 0 0 6.6 6.6l2.2-2.2a1 1 0 0 1 1-.25 11.4 11.4 0 0 0 3.6.6 1 1 0 0 1 1 1V20a1 1 0 0 1-1 1A17 17 0 0 1 3 4a1 1 0 0 1 1-1h3.5a1 1 0 0 1 1 1c0 1.25.2 2.45.6 3.6a1 1 0 0 1-.25 1z"/></svg>503 218 4471</li>
      <li><svg viewBox="0 0 24 24"><path d="M7 1h10a2 2 0 0 1 2 2v18a2 2 0 0 1-2 2H7a2 2 0 0 1-2-2V3a2 2 0 0 1 2-2zm0 3v14h10V4zm5 15.5a1.2 1.2 0 1 0 0 2.4 1.2 1.2 0 0 0 0-2.4z"/></svg>503 762 1958</li>
      <li><svg viewBox="0 0 24 24"><path d="M6 2h12v5H6zM3 8h18a2 2 0 0 1 2 2v7h-4v5H5v-5H1v-7a2 2 0 0 1 2-2zm4 7v5h10v-5z"/></svg>503 340 6612</li>
      <li><svg viewBox="0 0 24 24"><path d="M2 5h20v14H2zm2 2v.5l8 5 8-5V7z"/></svg>hello@meridiantrade.co</li>
    </ul>
  </section>

  <section class="card card-back">
    <div class="back-brand"><span class="back-brand-dot"></span>MERIDIAN</div>
    <p class="website">www.meridiantradeco.com</p>
  </section>
</main>
</body>
</html>
```